A clean crisp business card for a Landscape Construction company. Designed to be easy to read contact/ info and also be appealing/interesting, unlike a traditional business card.

Industry/Entity Type

Landscape Construction

Contact Information for Business Card

Company name : Brambleford Landscape Construction, phone number: (877) 62Vista, website:Bramblefordyards.example, Email, sales@bramblefordyards.example

Requirements
Nice to have
• Luxurious finishes/ details…. Icons or emblems next to contact info
Should not have
• Clipart or general pictures

```html
<!DOCTYPE html>
<html lang="en">
<head>
<meta charset="utf-8">
<title>Brambleford Landscape Construction – Business Cards</title>
<link rel="stylesheet" href="https://fonts.googleapis.com/css2?family=Cinzel:wght@500;600&family=Open+Sans:wght@400;600;700&display=swap">
<style>
  :root {
    --blue: #3d78c2;
    --green: #8cc63f;
    --ink: #2b2b2b;
    --card: #ffffff;
    --backdrop: #e9e6e1;
  }
  * { box-sizing: border-box; margin: 0; padding: 0; }
  html, body { width: 1200px; height: 913px; overflow: hidden; }
  body { background: var(--backdrop); position: relative; font-family: "Open Sans", Arial, sans-serif; }

  .card {
    position: absolute;
    width: 540px; height: 309px;
    background: var(--card);
    box-shadow: 0 10px 28px rgba(0,0,0,.18);
    overflow: hidden;
  }
  .card--front { left: 70px; top: 110px; }
  .card--back  { left: 590px; top: 494px; }

  .wordmark { display: flex; align-items: center; gap: 12px; }
  .wordmark__dot { width: 18px; height: 18px; border-radius: 50%; background: var(--green); flex: none; }
  .wordmark__name {
    font-family: "Cinzel", Georgia, serif; font-weight: 600; color: var(--blue);
    line-height: 1.05; letter-spacing: .02em;
  }
  .wordmark__name span { display: block; }

  .card--front .wordmark { position: absolute; left: 92px; top: 100px; }
  .card--front .wordmark__name { font-size: 34px; }
  .card--front .wordmark__name .sub { font-size: 15.5px; letter-spacing: .2em; margin-top: 6px; }
  .front__url {
    position: absolute; left: 0; right: 0; top: 226px; text-align: center;
    color: var(--blue); font-weight: 700; font-size: 14px; letter-spacing: .02em;
  }

  .card--back .wordmark { position: absolute; left: 30px; top: 118px; gap: 9px; }
  .card--back .wordmark__name { font-size: 22px; }
  .card--back .wordmark__name .sub { font-size: 10px; letter-spacing: .2em; margin-top: 5px; }

  .divider { position: absolute; left: 262px; top: 60px; width: 10px; height: 190px; }
  .divider__main { position: absolute; left: 4px; top: 18px; width: 3px; height: 128px; background: var(--blue); }
  .divider__thin { position: absolute; left: 0; width: 1px; height: 44px; background: var(--green); }
  .divider__thin--top { top: 0; }
  .divider__thin--bottom { top: 146px; left: 9px; }

  .contact { position: absolute; left: 292px; top: 56px; right: 18px; color: var(--ink); }
  .contact__name { font-family: "Cinzel", Georgia, serif; font-weight: 600; font-size: 22px; letter-spacing: .04em; }
  .contact__first { color: var(--blue); }
  .contact__last { color: var(--green); }
  .contact__role { font-size: 11.5px; margin-top: 2px; }
  .contact__address { font-size: 11px; line-height: 1.55; margin-top: 10px; }
  .contact__list { list-style: none; margin-top: 12px; font-size: 11px; line-height: 1.75; }
  .contact__list li { display: flex; align-items: center; gap: 7px; }
  .contact__list svg { width: 11px; height: 11px; flex: none; fill: var(--green); }

  .edge { position: absolute; left: 0; right: 0; bottom: 0; height: 12px; background: var(--green); border-top: 3px solid var(--blue); }
</style>
</head>
<body>

<section class="card card--front" aria-label="Card front">
  <div class="wordmark">
    <span class="wordmark__dot"></span>
    <p class="wordmark__name"><span>Brambleford</span><span class="sub">Landscape Construction</span></p>
  </div>
  <p class="front__url">www.Bramblefordyards.example</p>
</section>

<section class="card card--back" aria-label="Card back">
  <div class="wordmark">
    <span class="wordmark__dot"></span>
    <p class="wordmark__name"><span>Brambleford</span><span class="sub">Landscape Construction</span></p>
  </div>

  <div class="divider" aria-hidden="true">
    <span class="divider__thin divider__thin--top"></span>
    <span class="divider__main"></span>
    <span class="divider__thin divider__thin--bottom"></span>
  </div>

  <div class="contact">
    <h1 class="contact__name"><span class="contact__first">Rowan</span> <span class="contact__last">Hale</span></h1>
    <p class="contact__role">Director</p>
    <p class="contact__address">4127 Millbrook Ridge Rd.,<br>Suite 310, Fairhaven, OH 45811</p>
    <ul class="contact__list">
      <li><svg viewBox="0 0 24 24" aria-hidden="true"><path d="M6.6 10.8a15 15 0 0 0 6.6 6.6l2.2-2.2a1 1 0 0 1 1-.25 11.4 11.4 0 0 0 3.6.57 1 1 0 0 1 1 1V20a1 1 0 0 1-1 1A17 17 0 0 1 3 4a1 1 0 0 1 1-1h3.5a1 1 0 0 1 1 1c0 1.25.2 2.45.57 3.57a1 1 0 0 1-.25 1z"/></svg>(877) 62Vista</li>
      <li><svg viewBox="0 0 24 24" aria-hidden="true"><path d="M2 5h20v14H2zm2 2v.5l8 5 8-5V7l-8 5z"/></svg>sales@bramblefordyards.example</li>
      <li><svg viewBox="0 0 24 24" aria-hidden="true"><path d="M12 2a10 10 0 1 0 0 20 10 10 0 0 0 0-20zm6.9 9h-3a15 15 0 0 0-1.3-5.6A8 8 0 0 1 18.9 11zM12 4c.9 1.2 1.7 3.7 1.9 7h-3.8c.2-3.3 1-5.8 1.9-7zM4.1 13h3a15 15 0 0 0 1.3 5.6A8 8 0 0 1 4.1 13zm3-2h-3a8 8 0 0 1 4.3-5.6A15 15 0 0 0 7.1 11zM12 20c-.9-1.2-1.7-3.7-1.9-7h3.8c-.2 3.3-1 5.8-1.9 7zm2.6-1.4a15 15 0 0 0 1.3-5.6h3a8 8 0 0 1-4.3 5.6z"/></svg>www.bramblefordyards.example</li>
    </ul>
  </div>

  <div class="edge" aria-hidden="true"></div>
</section>

</body>
</html>
```